We’re a real estate firm that has landed a big builder in a neighboring state. Our branding needs...

We are a real estate firm who represents various builders along with doing resale here in Oregon. Our firm is growing to represent a big builder in Washington State and we’ll have another 40 brokers on our team. We need rebranding. As in, a new logo ( the house logo we have now looks cartoonish, hate it). We need new cards, something to really stand out. I’ve been thinking of using those NFC cards from ZEP or the ones with the seam color. I likely want two or three designs, a darker (as in a background color of black or grey) , a light one ( again I mean background color) and a credit card style (either plastic w an embossed name/number on front, or metal ). I’m thinking dark background for cc, or silver if it’s metal. That’s my thoughts, but you are the artists, so maybe you have an idea I haven’t considered. Our colors were black and red, but we don’t have to stick to that. Just nothing too busy. Oh, and we are typically representing the local, higher quality builders in our area (just below custom), but not national. Subdivisions are near the Kell Varney, Brisco, and Thornfield Crest sites. We are super excited, but without a lot of time to change the “look” of our brokerage. So I’ll be deciding and moving forward within 24 hours tops. Our name is Real Estate Summit Alliance ( we cant change the name because of timeline and business license) Thank you!

Industry/Entity Type

Real Estate

Contact Information for Business Card

The usual. Name of firm. Name of cardholder. Contact info.

Font styles to use
Serif
Sans Serif

Colors

Designer to choose colors to be used in the design.

Requirements
Must have
• A sleek or simple look. I included photos of cards with stylistic attributes we like. Thank you
Nice to have
• We really like the black backgrounds. With foil or embossed detail. We also like the black on black. Matte black card with raised shiny black detail. But still eye catching.
Should not have
• No ornate or busy looking style. We don’t want anything cluttered.

```html
<!DOCTYPE html>
<html lang="en">
<head>
<meta charset="utf-8">
<title>Real Estate Summit Alliance – Business Cards</title>
<link href="https://fonts.googleapis.com/css2?family=Work+Sans:wght@400;500;600&display=swap" rel="stylesheet">
<style>
  :root {
    --backdrop: #1c1c1c;
    --card: #262626;
    --card-front: #222222;
    --emboss: #3a3a3a;
    --white: #f4f4f4;
    --red: #d42a2f;
    --muted: #e6e6e6;
  }
  * { margin: 0; padding: 0; box-sizing: border-box; }
  html, body { width: 1200px; height: 900px; overflow: hidden; }
  body {
    background: var(--backdrop);
    font-family: "Work Sans", Arial, sans-serif;
    position: relative;
  }
  .card {
    position: absolute;
    left: 320px;
    width: 560px;
    height: 320px;
    border-radius: 4px;
  }
  .card-front {
    top: 110px;
    background: var(--card-front);
    display: flex;
    align-items: center;
    justify-content: center;
  }
  .front-wordmark {
    color: var(--emboss);
    font-size: 34px;
    font-weight: 500;
    text-align: center;
    line-height: 1.15;
  }
  .card-back {
    top: 470px;
    background: var(--card);
  }
  .back-wordmark {
    position: absolute;
    left: 34px;
    top: 120px;
    width: 220px;
    color: var(--white);
    font-size: 25px;
    font-weight: 500;
    line-height: 1.15;
    display: flex;
    align-items: flex-start;
    gap: 10px;
  }
  .wordmark-square {
    flex: none;
    width: 20px;
    height: 20px;
    margin-top: 5px;
    background: var(--white);
  }
  .divider {
    position: absolute;
    left: 292px;
    top: 80px;
    width: 2px;
    height: 180px;
    background: var(--white);
  }
  .contact {
    position: absolute;
    left: 318px;
    top: 80px;
    color: var(--muted);
  }
  .holder-name {
    color: var(--red);
    font-size: 24px;
    font-weight: 500;
    letter-spacing: 1.5px;
    text-transform: uppercase;
  }
  .holder-title { font-size: 14px; margin-top: 0; letter-spacing: 0.5px; }
  .address { font-size: 14px; line-height: 1.45; margin-top: 14px; letter-spacing: 0.5px; }
  .lines { list-style: none; margin-top: 10px; font-size: 14px; line-height: 1.5; letter-spacing: 0.5px; }
  .lines li { display: flex; align-items: center; gap: 8px; }
  .lines svg { width: 11px; height: 11px; flex: none; }
</style>
</head>
<body>
  <section class="card card-front">
    <div class="front-wordmark">Real Estate<br>Summit Alliance</div>
  </section>

  <section class="card card-back">
    <div class="back-wordmark">
      <span class="wordmark-square"></span>
      <span>Real Estate Summit Alliance</span>
    </div>
    <div class="divider"></div>
    <div class="contact">
      <div class="holder-name">Darren Holt</div>
      <div class="holder-title">Director</div>
      <div class="address">4150 NE Alder Ridge Dr.<br>Suite 305-B,<br>Fairview, OR 97024</div>
      <ul class="lines">
        <li>
          <svg viewBox="0 0 12 12" aria-hidden="true"><path d="M2.5 1 L4.5 1 L5.2 3.6 L4 4.6 Q5 7 7.4 8 L8.4 6.8 L11 7.5 L11 9.5 Q10.5 11 8.5 11 Q1 10 1 3.5 Q1 1.5 2.5 1 Z" fill="var(--red)"/></svg>
          (503) 555-0142
        </li>
        <li>
          <svg viewBox="0 0 12 12" aria-hidden="true"><rect x="1" y="2.5" width="10" height="7" fill="none" stroke="var(--red)" stroke-width="1.2"/><path d="M1 2.5 L6 6.5 L11 2.5" fill="none" stroke="var(--red)" stroke-width="1.2"/></svg>
          owenmarlow7@mailbox.com
        </li>
        <li>
          <svg viewBox="0 0 12 12" aria-hidden="true"><circle cx="6" cy="6" r="5" fill="none" stroke="var(--red)" stroke-width="1.1"/><ellipse cx="6" cy="6" rx="2.2" ry="5" fill="none" stroke="var(--red)" stroke-width="1"/><path d="M1 6 H11" stroke="var(--red)" stroke-width="1"/></svg>
          www.ridgeparcels.com
        </li>
      </ul>
    </div>
  </section>
</body>
</html>
```